English and Spanish Language School Needs a Business Card

Need a business card design a startup company called Maribel Language School. The company will offer English and Spanish conversational level courses designed to make the learner feel comfortable with grammar and vocabulary. We would like to see a logo with some colour that should communicate learning, growth.

Target Market(s)

Consumers and businesses

Industry/Entity Type

Education

Contact Information for Business Card

TBD

Font styles to use
Serif

Requirements
Must have
• Include the following
• Logo
• Name
• Title
• Cellphone Number
• Office Phone number
• Email address
• Office Address

```html
<!DOCTYPE html>
<html lang="en">
<head>
<meta charset="utf-8">
<title>Maribel Language School – Business Card</title>
<link rel="stylesheet" href="https://fonts.googleapis.com/css2?family=Montserrat:wght@400;500;600;700&display=swap">
<style>
  :root {
    --stage: #ece9e6;
    --card-white: #ffffff;
    --brand-red: #d42a35;
    --brand-red-dark: #b81d28;
    --ink: #1f2624;
    --swoosh: #263230;
    --back-top: #2f4a45;
    --back-bottom: #0d1413;
    --muted: #555b59;
  }
  * { box-sizing: border-box; margin: 0; padding: 0; }
  html, body {
    width: 1200px; height: 913px; overflow: hidden;
    background: var(--stage);
    font-family: "Montserrat", Arial, sans-serif;
  }
  .canvas {
    position: relative; width: 1200px; height: 913px;
    display: flex; align-items: center; justify-content: center; gap: 40px;
  }
  .card {
    position: relative; width: 540px; height: 309px;
    border-radius: 16px; overflow: hidden;
    box-shadow: 0 10px 28px rgba(0,0,0,.18);
  }
  /* Front */
  .card-front { background: var(--card-white); }
  .card-front .shapes { position: absolute; inset: 0; }
  .front-brand { position: absolute; left: 36px; top: 92px; width: 205px; }
  .brand-name {
    color: var(--brand-red); font-weight: 700; font-size: 46px;
    line-height: 1; letter-spacing: -1px;
  }
  .brand-sub {
    color: var(--brand-red); font-weight: 700; font-size: 15px;
    margin-top: 4px; padding-left: 30px;
  }
  .brand-rule { height: 1px; background: var(--ink); margin-top: 6px; width: 200px; }
  .person { position: absolute; left: 40px; top: 198px; }
  .person-name { font-weight: 700; font-size: 18px; color: var(--ink); letter-spacing: .3px; white-space: nowrap; }
  .person-title { font-size: 12px; color: var(--muted); margin-top: 2px; }
  .contact {
    position: absolute; right: 22px; top: 92px;
    color: #fff; text-align: right; font-size: 12.5px; line-height: 1.45;
  }
  .contact .row { display: flex; justify-content: flex-end; align-items: center; gap: 8px; }
  .contact .row svg { width: 10px; height: 10px; flex: none; }
  .contact .spacer { width: 10px; flex: none; }
  .contact .web { font-weight: 700; }
  /* Back */
  .card-back {
    background: linear-gradient(160deg, var(--back-top) 0%, #18241f 50%, var(--back-bottom) 100%);
    color: #fff;
  }
  .back-brand { position: absolute; left: 120px; top: 88px; }
  .back-brand .brand-name { color: #fff; font-size: 72px; }
  .back-brand .brand-sub { color: #fff; font-size: 21px; font-weight: 700; padding-left: 60px; }
  .back-web {
    position: absolute; left: 0; right: 0; bottom: 54px;
    text-align: center; font-size: 14px; font-weight: 600; letter-spacing: .5px;
  }
</style>
</head>
<body>
<main class="canvas">
  <section class="card card-front" aria-label="Business card front">
    <svg class="shapes" viewBox="0 0 540 309" preserveAspectRatio="none" aria-hidden="true">
      <defs>
        <linearGradient id="redPanel" x1="0" y1="0" x2="0" y2="1">
          <stop offset="0" stop-color="#e0404a"/>
          <stop offset="1" stop-color="#b81d28"/>
        </linearGradient>
      </defs>
      <path d="M334 0 C305 150 225 262 118 309 L162 309 C242 262 318 150 343 0 Z" fill="var(--swoosh)"/>
      <path d="M349 0 L540 0 L540 309 L170 309 C250 262 324 150 349 0 Z" fill="url(#redPanel)"/>
    </svg>
    <div class="front-brand">
      <div class="brand-name">Maribel</div>
      <div class="brand-sub">Language School</div>
      <div class="brand-rule"></div>
    </div>
    <div class="person">
      <div class="person-name">Lorna Whitfield</div>
      <div class="person-title">Director</div>
    </div>
    <div class="contact">
      <div class="row"><span>PO Box 218</span><span class="spacer"></span></div>
      <div class="row"><span>Ashbury VIC 3950</span><span class="spacer"></span></div>
      <div class="row"><span>+330 2471-0938</span>
        <svg viewBox="0 0 10 10"><rect x="2.5" y="0.5" width="5" height="9" rx="1" fill="none" stroke="#fff"/></svg></div>
      <div class="row"><span>+330 2485-1672</span>
        <svg viewBox="0 0 10 10"><path d="M2 1 L4 1 L5 3.5 L3.8 4.5 C4.5 6 5 6.5 6.5 7.2 L7.5 6 L10 7 L10 9 C5 9.5 0.5 5 2 1 Z" fill="#fff"/></svg></div>
      <div class="row"><span>hello@maribelschool.com</span>
        <svg viewBox="0 0 10 10"><rect x="0.5" y="2" width="9" height="6" fill="none" stroke="#fff"/><path d="M0.5 2 L5 5.5 L9.5 2" fill="none" stroke="#fff"/></svg></div>
      <div class="row"><span class="web">maribelschool.com</span>
        <svg viewBox="0 0 10 10"><circle cx="5" cy="5" r="4.3" fill="none" stroke="#fff"/><path d="M0.7 5 H9.3 M5 0.7 C2.5 3 2.5 7 5 9.3 M5 0.7 C7.5 3 7.5 7 5 9.3" fill="none" stroke="#fff" stroke-width=".7"/></svg></div>
    </div>
  </section>

  <section class="card card-back" aria-label="Business card back">
    <div class="back-brand">
      <div class="brand-name">Maribel</div>
      <div class="brand-sub">Language School</div>
    </div>
    <div class="back-web">www.maribelschool.com</div>
  </section>
</main>
</body>
</html>
```